KVR Inc Web Design

WHAT ARE WE DOING?
We are developing a new website look and feel for a new company called KVR Inc. This new look and feel should include colors, design elements, choice of photography and other imagery, fonts, and other user experience elements.

WHAT DO THEY DO?
KVR, Inc, makes tools for researchers who are studying protein-protein interactions. These molecules are the basic tools of biology, and serve as key targets for drug developers and disease researchers. The world of proteins is enormously complex, and companies like KVR provide researchers with critical tools that help them elucidate this world.

WHO ARE WE TALKING TO?
The target audience for this website are professional scientists working in university research or biopharma drug development. They are highly sophisticated consumers looking for key tools that will advance their research.

WHAT DO WE WANT THEM TO DO?
The site is an information resource for the customer exploring the tools that KVR sells and the scientific issues surrounding protein-protein interactions. They should be able to navigate easily to their content of choice, while the whole site should convey a professionalism that enhanced KVR’s credibility.

WHAT DOES THE KVR BRAND STAND FOR?
KVR stands for illumination. Proteins are challenging to study, and KVR exists to help shed light on their workings.

WHAT ARE THE KEY VALUES OF THE KVR BRAND?
Integrity. Innovation. Insight.

WHAT ARE THE EXECUTIONAL MANDITORIES?
The look and feel is completely up for grabs. Nothing is off the table.

WHAT ARE THE DELIVERABLES?
We need new designs for the following templates:
http://cms.marlowbench.com/
http://cms.marlowbench.com/products-and-services/instruments-3/bench-top-instruments/
http://cms.marlowbench.com/category/lab-study/

```html
<!DOCTYPE html>
<html lang="en">
<head>
<meta charset="utf-8">
<title>KVR Inc — Featured Report</title>
<link rel="stylesheet" href="https://fonts.googleapis.com/css2?family=Mulish:wght@400;600;700&display=swap">
<style>
:root{
  --orange:#f7a833;
  --blue:#2eaed6;
  --text:#555;
  --muted:#666;
  --line:#d9d9d9;
  --bar:#a3a3a3;
  --footer:#737373;
  --white:#fff;
}
*{box-sizing:border-box;margin:0;padding:0}
html,body{width:1092px;height:1200px;overflow:hidden;background:#fff}
body{font-family:"Mulish",Arial,sans-serif;color:var(--text)}
.page{position:absolute;left:0;top:0;width:1280px;height:1406px;transform:scale(.853125);transform-origin:0 0;overflow:hidden}
.abs{position:absolute}
a{color:inherit;text-decoration:none}

.site-header{left:0;top:0;width:1280px;height:66px;border-top:3px solid var(--orange);border-bottom:1px solid #e6e6e6}
.brand{left:128px;top:13px;font-size:30px;font-weight:400;letter-spacing:6px;color:#666}
.main-nav{left:0;top:0;width:1280px;height:60px;font-size:16px;font-weight:700;color:var(--text);letter-spacing:-.2px}
.main-nav a{position:absolute;top:20px;white-space:nowrap}
.main-nav .active{color:var(--orange)}
.search{left:1005px;top:17px;width:147px;height:27px;background:linear-gradient(90deg,#7d7d7d,#959595);color:#ddd;font-size:14px;padding:5px 8px}
.search svg{position:absolute;right:7px;top:7px}

.featured-icon{left:129px;top:91px}
.featured-title{left:173px;top:98px;font-size:30px;font-weight:400;color:var(--text);letter-spacing:.5px}
.rule-double{height:4px;border-top:1px solid var(--line);border-bottom:1px solid var(--line)}
.report-name{left:127px;top:165px;font-size:23px;color:var(--text)}
.report-link{left:540px;top:168px;font-size:19px;color:var(--orange)}

.filter-bar{left:127px;top:209px;width:1025px;height:62px;background:var(--bar)}
.field{position:absolute;top:18px;height:27px;background:#fff;color:#aaa;font-size:14px;padding:5px 16px}
.field .caret{position:absolute;right:14px;top:10px;width:0;height:0;border-left:7px solid transparent;border-right:7px solid transparent;border-top:8px solid #999}
.btn{background:var(--orange);color:#fff;font-weight:700;text-align:center}
.filter-btn{position:absolute;left:865px;top:18px;width:135px;height:27px;font-size:15px;line-height:27px}
.filter-btn svg{vertical-align:-1px;margin-right:4px}

.sidebar-shade{left:300px;top:295px;width:64px;height:1000px;background:linear-gradient(90deg,rgba(245,245,245,0),#f4f4f4)}
.side-head{font-size:20px;font-weight:700;color:var(--blue);line-height:1}
.side-list{left:127px;top:347px;width:236px;list-style:none}
.side-list li{height:36px;border-bottom:1px solid #e4e4e4;font-size:17px;line-height:36px;padding-left:14px;position:relative}
.side-list li::before{content:"»";position:absolute;left:0;font-size:13px;top:-1px}
.side-list li.active{color:var(--orange)}
.side-list li.active::after{content:"⟶";position:absolute;right:12px;font-size:16px}
.promo-img{left:128px;top:742px;width:215px;height:215px;background:linear-gradient(135deg,#eef3f8,#b9c9dc 60%,#e89a55)}
.promo-text{left:127px;top:967px;width:220px;font-size:14.5px;line-height:18px;color:var(--text)}
.promo-btn{left:127px;top:1036px;width:135px;height:27px;font-size:15px;line-height:27px;font-weight:400}
.loc-text{left:126px;top:1141px;width:230px;font-size:14.5px;line-height:18px}

.order-tab{left:389px;top:307px;width:80px;height:29px;background:var(--bar);color:#fff;font-size:14px;line-height:29px;padding-left:15px}
.order-tab::after{content:"";position:absolute;right:-8px;top:7px;border-top:8px solid transparent;border-bottom:8px solid transparent;border-left:8px solid var(--bar)}
.order-links{left:499px;top:313px;font-size:14px;color:var(--orange);display:flex;gap:11px}

.card{position:absolute;width:237px}
.thumb{width:237px;height:184px;border:1px solid #ddd;padding:6px;background:#fff}
.thumb div{width:100%;height:100%}
.card h3{font-size:15.5px;font-weight:700;color:var(--blue);line-height:19px;margin-top:11px}
.card p{font-size:13.5px;line-height:18px;margin-top:4px;color:var(--text)}
.card p+p{margin-top:0}
.card .more{display:block;font-size:13.5px;color:var(--orange);margin-top:4px}

.lab-a{background:linear-gradient(135deg,#e7ecf2,#b8c7d8 55%,#6d8fb8)}
.lab-b{background:linear-gradient(135deg,#dfe9f2,#f4eee8 50%,#c7d7e6)}
.pipette{background:linear-gradient(180deg,#2a9ec9,#6fd0ee 55%,#1d82b5)}
.animal{background:radial-gradient(ellipse at 55% 55%,#8d8782 0,#c8c4c0 35%,#fff 60%)}
.plant{background:linear-gradient(135deg,#d4e4f0,#a9c3da 50%,#e8eef4)}
.team{background:linear-gradient(135deg,#f1f1f1,#d9dde2 50%,#a8b9cb)}

.site-footer{left:0;top:1339px;width:1280px;height:67px;background:var(--footer);color:#fff}
.foot-nav{position:absolute;left:128px;top:27px;font-size:14px}
.social{position:absolute;left:879px;top:22px;display:flex;gap:5px}
.social span{width:27px;height:27px;border-radius:50%;background:#fff}
.copy{position:absolute;left:991px;top:28px;font-size:15px}
.copy b{font-weight:400;color:var(--orange)}
</style>
</head>
<body>
<div class="page">
  <header class="site-header abs">
    <div class="brand abs">KVR INC</div>
    <nav class="main-nav abs">
      <a style="left:326px">Company</a><a class="active" style="left:425px">Products &amp; Services</a><a style="left:600px">Learning Center</a><a style="left:747px">Events</a><a style="left:823px">KVR News</a><a style="left:920px">Contact</a>
    </nav>
    <div class="search abs">Search
      <svg width="13" height="13" viewBox="0 0 13 13"><circle cx="5" cy="5" r="4" fill="none" stroke="#ccc" stroke-width="1.5"/><path d="M8 8l4 4" stroke="#ccc" stroke-width="1.5"/></svg>
    </div>
  </header>

  <svg class="featured-icon abs" width="33" height="36" viewBox="0 0 33 36">
    <rect x="1.5" y="5" width="30" height="29" fill="none" stroke="#666" stroke-width="2"/>
    <rect x="11" y="1" width="11" height="7" fill="#fff" stroke="#666" stroke-width="2"/>
    <rect x="8" y="22" width="4" height="7" fill="#666"/><rect x="14" y="17" width="4" height="12" fill="#666"/><rect x="20" y="13" width="4" height="16" fill="#666"/>
  </svg>
  <h1 class="featured-title abs">FEATURED REPORT</h1>
  <div class="rule-double abs" style="left:127px;top:138px;width:1025px"></div>

  <div class="report-name abs">Screening assays for GPCR ligands 3</div>
  <a class="report-link abs">Read &amp; Download ➜</a>

  <form class="filter-bar abs">
    <div class="field" style="left:23px;width:277px">Keyword</div>
    <div class="field" style="left:311px;width:257px">Topic<span class="caret"></span></div>
    <div class="field" style="left:580px;width:267px">Media Types<span class="caret"></span></div>
    <div class="btn filter-btn"><svg width="12" height="12" viewBox="0 0 13 13"><circle cx="5" cy="5" r="4" fill="none" stroke="#fff" stroke-width="1.8"/><path d="M8 8l4 4" stroke="#fff" stroke-width="1.8"/></svg>Search Now</div>
  </form>

  <div class="sidebar-shade abs"></div>

  <aside>
    <h2 class="side-head abs" style="left:127px;top:309px">Product Overview</h2>
    <div class="rule-double abs" style="left:127px;top:341px;width:236px"></div>
    <ul class="side-list abs">
      <li>Application Note</li><li class="active">Manual</li><li>PDF’s</li><li>Report</li><li>White Paper</li><li>Pipette Calibration</li><li>Application Note</li><li style="border:0">Common Errors</li>
    </ul>

    <h2 class="side-head abs" style="left:126px;top:666px;font-size:19px;line-height:20px">Ready to save time<br>in your lab?</h2>
    <div class="rule-double abs" style="left:127px;top:716px;width:236px"></div>
    <div class="promo-img abs" role="img" aria-label="Automated laboratory instrument close-up"></div>
    <p class="promo-text abs">to have a member of our team Demo what KVR's instruments could do for you.</p>
    <a class="btn promo-btn abs">Click Here</a>

    <h2 class="side-head abs" style="left:126px;top:1095px">Location</h2>
    <div class="rule-double abs" style="left:127px;top:1124px;width:236px"></div>
    <p class="loc-text abs">Lorem ipsum dolor sit amet nisl consectetur adipiscing elit</p>
  </aside>

  <div class="order-tab abs">Order by</div>
  <div class="order-links abs"><span>DATE</span><span>|</span><span>TITLE</span><span style="margin-left:6px">ASCENDING▼</span><span style="margin-left:24px">DESCENDING▲</span></div>

  <main>
    <article class="card" style="left:390px;top:356px">
      <div class="thumb"><div class="lab-a" role="img" aria-label="Scientist at a laboratory microscope"></div></div>
      <h3>Sample Prep Checklist</h3><p>Dr. Thomas Avery, Aug 2013</p><p>Application Note, Manual</p><a class="more">Read More ➜</a>
    </article>
    <article class="card" style="left:653px;top:356px">
      <div class="thumb"><div class="lab-b" role="img" aria-label="Researchers working in a bright lab"></div></div>
      <h3>Screening Assays for GPCR...</h3><p>Dr. Helen Marsh, Aug 2013</p><p>Application Note, Video</p><a class="more">Read More ➜</a>
    </article>
    <article class="card" style="left:916px;top:356px">
      <div class="thumb"><div class="pipette" role="img" aria-label="Pipette tips over a blue well plate"></div></div>
      <h3>Lorem ipsum dolor sit amet, consectetur adipiscing elit</h3><p>Halden University, July 2013</p><p>Manual, Report</p><a class="more">Read More ➜</a>
    </article>

    <article class="card" style="left:390px;top:674px">
      <div class="thumb"><div class="animal" role="img" aria-label="Laboratory mouse on white"></div></div>
      <h3>Nam venenatis nisl libero</h3><p>Halden University, July 2013</p><p>Manual, Report</p><a class="more">Read More ➜</a>
    </article>
    <article class="card" style="left:653px;top:674px">
      <div class="thumb"><div class="plant" role="img" aria-label="Researchers examining a plant sample"></div></div>
      <h3>Duis aliquam purus sed nulla faucibus</h3><p>Paul Deneuve PHD</p><a class="more">Read More ➜</a>
    </article>
    <article class="card" style="left:916px;top:674px">
      <div class="thumb"><div class="plant" role="img" aria-label="Researchers examining a plant sample"></div></div>
      <h3>Sample Prep Checklist</h3><p>Dr. Thomas Avery, Aug 2013</p><p>Application Note, Manual</p><a class="more">Read More ➜</a>
    </article>

    <article class="card" style="left:390px;top:995px">
      <div class="thumb"><div class="lab-a" role="img" aria-label="Scientist at a laboratory microscope"></div></div>
      <h3>Lorem ipsum dolor sit amet nisl consectetur adipiscing elit</h3><p>Dr. Thomas Avery, Aug 2013</p><p>PDF, White Paper</p><a class="more">Read More ➜</a>
    </article>
    <article class="card" style="left:653px;top:995px">
      <div class="thumb"><div class="lab-b" role="img" aria-label="Researchers working in a bright lab"></div></div>
      <h3>Screening Assays for GPCR...</h3><p>Dr. Thomas Avery, Aug 2013</p><p>Application Note, Manual</p><a class="more">Read More ➜</a>
    </article>
    <article class="card" style="left:916px;top:995px">
      <div class="thumb"><div class="team" role="img" aria-label="Team of researchers in safety goggles"></div></div>
      <h3>Nam venenatis nisl libero</h3><p>Dr. Thomas Avery, Aug 2013</p><p>Application Note, Manual</p><a class="more">Read More ➜</a>
    </article>
  </main>

  <footer class="site-footer abs">
    <nav class="foot-nav">Company &nbsp;-&nbsp; Products &amp; Services &nbsp;-&nbsp; Learning Center &nbsp;-&nbsp; Events &nbsp;-&nbsp; KVR News &nbsp;-&nbsp; Contact</nav>
    <div class="social"><span></span><span></span><span></span></div>
    <div class="copy">Copyright © <b>KVR Inc.</b> 2013</div>
  </footer>
</div>
</body>
</html>
```